Irrigation Business needs their business cards modernised and revamped

I would like to keep my current logo, colours and revamp the format of the card.

I would like the card to be clean yet important.

Im not sure if you include texture but i would like the named logo to be indented into the card etc.

show me something alive and free something thats clinical to the point yet has a feel of achievement. i would like people to go nice card.

Target Market(s)

high end clients, corporate, sports field manger, the guys that make the decisions

Industry/Entity Type

Business

Contact Information for Business Card

nformation to be included

Dean Harlow (Director)
0487305526
dean@kolvat.biz
www.kestonfieldworks.com

instagram logo
google logo
facebook logo

Colors

Designer to choose colors to be used in the design.

Requirements
Nice to have
• indentations a really nice feel to the card good texture

```html
<!DOCTYPE html>
<html lang="en">
<head>
<meta charset="utf-8">
<title>Keston Fieldworks – Business Cards</title>
<link href="https://fonts.googleapis.com/css2?family=Open+Sans:wght@400;600;700;800&display=swap" rel="stylesheet">
<style>
  :root {
    --backdrop: #2c2c2f;
    --card-white: #f7f7f5;
    --brand-blue: #1c5fae;
    --brand-blue-deep: #0f4f9e;
    --sky-blue: #34a6da;
    --leaf-green: #3fae4a;
    --ink-white: #ffffff;
  }
  * { margin: 0; padding: 0; box-sizing: border-box; }
  html, body { width: 1200px; height: 840px; overflow: hidden; }
  body {
    background: var(--backdrop);
    font-family: "Open Sans", Arial, sans-serif;
    position: relative;
  }
  .card {
    position: absolute;
    width: 560px;
    height: 320px;
    background: var(--card-white);
    border-radius: 4px;
    overflow: hidden;
    box-shadow: 0 10px 28px rgba(0,0,0,0.45);
  }
  .card--front { left: 90px; top: 80px; }
  .card--back { left: 550px; top: 440px; }

  /* front */
  .brand {
    position: absolute;
    left: 0; right: 0; top: 62px;
    display: flex; flex-direction: column; align-items: center;
  }
  .brand__disc {
    width: 92px; height: 92px;
    border-radius: 50%;
    background: var(--sky-blue);
    border: 5px solid var(--brand-blue);
  }
  .brand__name {
    margin-top: 14px;
    font-weight: 800;
    font-size: 30px;
    letter-spacing: 0.5px;
    text-transform: uppercase;
    color: var(--brand-blue);
  }
  .social {
    margin-top: 14px;
    display: flex; gap: 6px;
  }
  .social__dot {
    width: 16px; height: 16px;
    border-radius: 50%;
    background: var(--brand-blue);
  }

  /* back */
  .back-art { position: absolute; inset: 0; }
  .person {
    position: absolute;
    left: 40px; top: 118px;
    text-transform: uppercase;
    font-size: 14px;
    line-height: 1.3;
  }
  .person__name { color: var(--brand-blue); font-weight: 700; }
  .person__role { color: var(--leaf-green); font-weight: 400; }
  .contact {
    position: absolute;
    left: 40px; bottom: 30px;
    list-style: none;
    color: var(--ink-white);
    font-size: 13px;
    line-height: 1.45;
  }
  .contact__item { display: flex; align-items: center; gap: 8px; }
  .contact__icon { width: 12px; height: 12px; flex: none; }
</style>
</head>
<body>

<section class="card card--front">
  <div class="brand">
    <div class="brand__disc"></div>
    <div class="brand__name">Keston Fieldworks</div>
    <div class="social">
      <span class="social__dot"></span>
      <span class="social__dot"></span>
      <span class="social__dot"></span>
    </div>
  </div>
</section>

<section class="card card--back">
  <svg class="back-art" width="560" height="320" viewBox="0 0 560 320">
    <circle cx="420" cy="140" r="128" fill="none" stroke="var(--brand-blue)" stroke-width="6"/>
    <circle cx="420" cy="140" r="116" fill="var(--sky-blue)"/>
    <path d="M0 210 L560 150 L560 320 L0 320 Z" fill="var(--brand-blue-deep)" opacity="0.9"/>
  </svg>

  <div class="person">
    <div class="person__name">Dean Harlow</div>
    <div class="person__role">Director</div>
  </div>

  <ul class="contact">
    <li class="contact__item">
      <svg class="contact__icon" viewBox="0 0 12 12"><path d="M2 1h2.5l1 2.5-1.5 1a6 6 0 0 0 3.5 3.5l1-1.5L11 7.5V10a1 1 0 0 1-1 1A9 9 0 0 1 1 2a1 1 0 0 1 1-1z" fill="#fff"/></svg>
      0487305526
    </li>
    <li class="contact__item">
      <svg class="contact__icon" viewBox="0 0 12 12"><rect x="0.5" y="2" width="11" height="8" rx="1" fill="#fff"/><path d="M1 3l5 4 5-4" fill="none" stroke="#0f4f9e" stroke-width="1"/></svg>
      dean@kolvat.biz
    </li>
    <li class="contact__item">
      <svg class="contact__icon" viewBox="0 0 12 12"><circle cx="6" cy="6" r="5.2" fill="none" stroke="#fff" stroke-width="1.2"/><path d="M1 6h10M6 1c-2.5 3-2.5 7 0 10M6 1c2.5 3 2.5 7 0 10" fill="none" stroke="#fff" stroke-width="1"/></svg>
      www.kestonfieldworks.com
    </li>
  </ul>
</section>

</body>
</html>
```